Wine label Design

We are looking to develop an elegant contemporary Chilean design; for a new Wine Brand TORVENA to be sold in Chinese Market.
We would like to see designs that are a fine balance between having a traditional design that can offer quality reassurance and being distinctive enough to stand out on crowded shelves. The final design should be easy-to-remember and communicate Quality, Tradition and have a conection with Chile.

Target Market(s)

Urban Chinese between 25 to 40 yo

Requirements
Must have
• Paper label
Information on Front label : Grape (example Cabernet sauvignon) / Vintage (ex 2010) / Wine of Chile
Bottle shape is given (see attached)
Nice to have
• An element of uniqueness, easy to recall the brand
Red and Gold Color are appreciated by the Target
Should not have
• White background
Number 4 is considered death, should not be included on the design

```html
<!DOCTYPE html>
<html lang="en">
<head>
<meta charset="utf-8">
<title>TORVENA Wine Label</title>
<link rel="stylesheet" href="https://fonts.googleapis.com/css2?family=Cinzel:wght@600&family=Josefin+Sans:wght@600&family=Playfair+Display:ital@1&display=swap">
<style>
  :root {
    --backdrop: #1f1f1f;
    --label-red: #d9502f;
    --label-red-deep: #c8432a;
    --gold: #e3b33c;
    --gold-dark: #a9761c;
    --ink: #6e1e12;
    --rule: #8a3a28;
  }
  html, body {
    margin: 0;
    width: 1200px;
    height: 949px;
    overflow: hidden;
    background: var(--backdrop);
  }
  .canvas {
    position: relative;
    width: 1200px;
    height: 949px;
    display: flex;
    align-items: center;
    justify-content: center;
  }
  .label {
    position: relative;
    width: 880px;
    height: 330px;
    background: radial-gradient(ellipse at 50% 40%, var(--label-red) 0%, var(--label-red-deep) 100%);
    display: flex;
    flex-direction: column;
    align-items: center;
    justify-content: center;
    box-sizing: border-box;
  }
  .label__band {
    position: absolute;
    left: 0;
    right: 0;
    height: 8px;
    background: linear-gradient(180deg, var(--gold) 0%, var(--gold-dark) 100%);
  }
  .label__band--top { top: 10px; }
  .label__band--bottom { bottom: 10px; }
  .brand {
    display: flex;
    align-items: center;
    gap: 18px;
    margin-bottom: 22px;
  }
  .brand__dot {
    width: 22px;
    height: 22px;
    border-radius: 50%;
    background: var(--gold);
  }
  .brand__name {
    font-family: "Cinzel", serif;
    font-weight: 600;
    font-size: 78px;
    letter-spacing: 4px;
    color: var(--gold);
    line-height: 1;
  }
  .details {
    width: 320px;
    text-align: center;
    font-family: "Josefin Sans", sans-serif;
    font-weight: 600;
    font-size: 19px;
    letter-spacing: 2px;
    color: var(--ink);
  }
  .details__line {
    padding: 8px 0;
  }
  .details__line + .details__line {
    border-top: 1.5px solid var(--rule);
  }
  .grape {
    margin-top: 26px;
    font-family: "Playfair Display", serif;
    font-style: italic;
    font-size: 24px;
    letter-spacing: 1.5px;
    color: var(--ink);
  }
</style>
</head>
<body>
  <main class="canvas">
    <section class="label">
      <div class="label__band label__band--top"></div>
      <div class="brand">
        <span class="brand__name">TORVENA</span>
        <span class="brand__dot"></span>
      </div>
      <div class="details">
        <div class="details__line">Vintage 2010</div>
        <div class="details__line">Wine of Chile</div>
      </div>
      <div class="grape">Cabernet Sauvignon</div>
      <div class="label__band label__band--bottom"></div>
    </section>
  </main>
</body>
</html>
```